Marlow Estate Fixers (Handyman / Home Improvement Company)

Looking for a double sided professional looking business card with Logo attached to be highlighted on one side and throwing in an image of a handyman as an option would be nice to see as well. We are a company focused on providing quality Handyman and Home improvement services in a timely manner that is done right the first time with integrity

Industry/Entity Type

Handyman / Home Improvement

Contact Information for Business Card

(LOGO, Name, Mobile and office phone numbers, email) on front side of card, (the words "The SOLUTION to all of your Handyman and Home Improvement needs" followed by "Family Owned and Operated" at the very bottom) on the back.

Colors
EB3D1F
EC4F4E
F09395
F8D3D4
FCEDEE

Requirements
Must have
• Red, Gray, Black Color scheme
Should not have
• No Yellow or Blue colors

```html
<!DOCTYPE html>
<html lang="en">
<head>
<meta charset="utf-8">
<title>Marlow Estate Fixers – Business Card</title>
<link rel="stylesheet" href="https://fonts.googleapis.com/css2?family=Michroma&family=Montserrat:wght@400;500&family=Poppins:wght@500&display=swap">
<style>
  :root {
    --page-bg: #a9aaad;
    --card-black: #000000;
    --card-back-black: #05080a;
    --brand-red: #eb3d1f;
    --accent-red: #ec2f2f;
    --text-white: #f2f2f2;
    --mark-gray: #6f7073;
    --rule-gray: #4a4a4a;
    --figure-dark: #2a2a2a;
    --figure-red: #d8302f;
  }
  * { margin: 0; padding: 0; box-sizing: border-box; }
  html, body {
    width: 1194px; height: 1200px; overflow: hidden;
    background: var(--page-bg);
  }
  .card {
    position: absolute; left: 308px; width: 579px; height: 330px;
    overflow: hidden;
  }
  .card--front { top: 167px; background: var(--card-black); }
  .card--back { top: 639px; background: var(--card-back-black); }

  .holder-name {
    position: absolute; left: 40px; top: 55px;
    font-family: "Michroma", sans-serif; font-size: 17px; letter-spacing: 1.5px;
    color: var(--accent-red); font-weight: 400;
  }
  .holder-role {
    position: absolute; left: 41px; top: 91px;
    font-family: "Montserrat", sans-serif; font-weight: 500; font-size: 13px;
    letter-spacing: 2px; color: var(--text-white);
  }
  .role-rule {
    position: absolute; left: 105px; top: 99px; width: 313px; height: 1px;
    background: var(--rule-gray);
  }
  .company-name {
    position: absolute; font-family: "Michroma", sans-serif; text-align: center;
    line-height: 1.3;
  }
  .card--front .company-name {
    left: 420px; top: 42px; width: 134px; font-size: 13px; color: var(--mark-gray);
  }
  .card--back .company-name {
    left: 308px; top: 68px; width: 188px; font-size: 17px; color: var(--brand-red);
  }

  .contact-list {
    position: absolute; left: 44px; top: 220px; list-style: none;
    font-family: "Montserrat", sans-serif; font-size: 16px; letter-spacing: 1.4px;
    color: var(--text-white);
  }
  .contact-item { display: flex; align-items: center; height: 28px; }
  .contact-item svg { width: 18px; height: 18px; margin-right: 14px; flex: none; }

  .handyman-figure {
    position: absolute; left: 20px; top: 23px; width: 182px; height: 307px;
    background: linear-gradient(180deg, var(--figure-dark) 0%, var(--figure-dark) 72%, var(--figure-red) 72%, var(--figure-red) 100%);
    border-radius: 60px 60px 0 0;
    opacity: 0.9;
  }
  .tagline {
    position: absolute; left: 248px; top: 189px; width: 310px; text-align: center;
    font-family: "Michroma", sans-serif; font-size: 11.5px; letter-spacing: 2.2px;
    line-height: 25.5px; color: var(--text-white); text-transform: uppercase;
  }
  .family-line {
    position: absolute; left: 248px; top: 286px; width: 310px; text-align: center;
    font-family: "Poppins", sans-serif; font-weight: 500; font-size: 12.5px;
    letter-spacing: 2.4px; color: var(--accent-red);
  }
</style>
</head>
<body>
  <section class="card card--front">
    <h1 class="holder-name">DALE ASHWORTH</h1>
    <p class="holder-role">OWNER</p>
    <div class="role-rule"></div>
    <p class="company-name">Marlow Estate Fixers</p>
    <ul class="contact-list">
      <li class="contact-item">
        <svg viewBox="0 0 18 18" fill="none" stroke="var(--accent-red)" stroke-width="1.2"><circle cx="9" cy="9" r="8"/><path d="M6 5.2l1.5-.4 1 2.2-1 .8a5 5 0 002.7 2.7l.8-1 2.2 1-.4 1.5c-3.5.4-7.1-3.2-6.8-6.8z"/></svg>
        (555) 014-2286
      </li>
      <li class="contact-item">
        <svg viewBox="0 0 18 18" fill="none" stroke="var(--accent-red)" stroke-width="1.2"><circle cx="9" cy="9" r="8"/><rect x="6.3" y="4.3" width="5.4" height="9.4" rx="1"/><path d="M8.3 12h1.4"/></svg>
        (555) 014-2286
      </li>
      <li class="contact-item">
        <svg viewBox="0 0 18 18" fill="none" stroke="var(--accent-red)" stroke-width="1.2"><circle cx="9" cy="9" r="8"/><rect x="4.8" y="6" width="8.4" height="6" rx=".5"/><path d="M4.8 6.2L9 9.4l4.2-3.2"/></svg>
        daleashworth@mailbox.com
      </li>
    </ul>
  </section>

  <section class="card card--back">
    <div class="handyman-figure" role="img" aria-label="Illustration of a smiling handyman in a red cap and black shirt, arms crossed, holding a hammer, with a tool belt"></div>
    <p class="company-name">Marlow Estate Fixers</p>
    <p class="tagline">Your solution to all of<br>your handyman and home<br>improvement needs</p>
    <p class="family-line">Family Owned and Operated</p>
  </section>
</body>
</html>
```